Parcelwise HQ letterhead and envelope

Design a formal (8.5x11) letterhead and envelope for sales outreach and legal matters. Using design input from https://www.parcelwisehq.example/ and the attached documents.

Industry/Entity Type

Software Service

Requirements
Must have
• These 4 hex colors are our official colors:
• #355c98 [blue]
• #1eb1a2 [teal]
• #fdba12 [gold]
• #f1653b [orange]
• So no other colors besides these should be used.

```html
<!DOCTYPE html>
<html lang="en">
<head>
<meta charset="utf-8">
<title>Parcelwise HQ Letterhead</title>
<link href="https://fonts.googleapis.com/css2?family=Open+Sans:wght@400;600;700&display=swap" rel="stylesheet">
<style>
  :root {
    --brand-blue: #355c98;
    --ink: #1f1f1f;
    --paper: #ffffff;
    --backdrop: #ececec;
  }
  * { box-sizing: border-box; margin: 0; padding: 0; }
  html, body {
    width: 1200px; height: 784px; overflow: hidden;
    background: var(--backdrop);
    font-family: "Open Sans", sans-serif;
  }
  .letterhead {
    position: absolute; left: 314px; top: 20px;
    width: 572px; height: 744px;
    background: var(--paper);
    box-shadow: 0 2px 10px rgba(0,0,0,0.12);
    overflow: hidden;
  }
  .brand {
    position: absolute; left: 44px; top: 44px;
    display: flex; align-items: center; gap: 8px;
  }
  .brand-dot {
    width: 22px; height: 22px; border-radius: 50%;
    border: 2px solid var(--brand-blue);
  }
  .brand-name {
    font-size: 22px; font-weight: 400; color: var(--brand-blue);
    letter-spacing: 0.2px;
  }
  .letter-body {
    position: absolute; left: 112px; top: 120px; width: 400px;
    color: var(--ink); font-size: 10.5px; line-height: 1.5;
  }
  .salutation { font-weight: 700; font-size: 12px; margin-bottom: 10px; }
  .letter-body p { margin-bottom: 11px; }
  .signature {
    width: 110px; height: 40px; margin-top: 4px;
    background: linear-gradient(90deg, #f4f4f4, #e6e6e6);
    border-radius: 4px;
  }
  .footer-band {
    position: absolute; left: 0; bottom: 0; width: 100%; height: 72px;
    background: var(--brand-blue); color: var(--paper);
    padding: 12px 28px 0 28px; font-size: 9.5px; line-height: 1.4;
    white-space: nowrap;
  }
  .footer-company { font-weight: 700; font-size: 11px; }
  .footer-address { margin-top: 2px; }
  .footer-line { display: flex; align-items: center; gap: 18px; margin-top: 3px; }
  .contact-item { display: inline-flex; align-items: center; gap: 5px; }
  .contact-item svg { width: 10px; height: 10px; flex: none; }
</style>
</head>
<body>
  <main class="letterhead">
    <header class="brand">
      <span class="brand-dot"></span>
      <span class="brand-name">Parcelwise HQ</span>
    </header>

    <section class="letter-body">
      <p class="salutation">Dear Mr. Avery,</p>
      <p>Lorem Ipsum is simply dummy text of the printing and typesetting industry. Lorem Ipsum has been the industry's standard dummy text ever since the 1500s, when an unknown printer took a galley of type and scrambled it to make a type specimen book. It has survived not only five centuries, but also the leap into electronic typesetting, remaining essentially unchanged.</p>
      <p>The standard chunk of Lorem Ipsum used since the 1500s is reproduced below for those interested. Sections 1.10.32 and 1.10.33 from "de Finibus Bonorum et Malorum" by Cicero are also reproduced in their exact original form, accompanied by English versions from the 1914 translation by H. Rackham.</p>
      <p>Lorem Ipsum is simply dummy text of the printing and typesetting industry. Lorem Ipsum has been the industry's standard dummy text ever since the 1500s, when an unknown printer took a galley of type and scrambled it to make a type specimen book. It has survived not only five centuries, but also the leap into electronic typesetting, remaining essentially unchanged. It was popularised in the</p>
      <p>The standard chunk of Lorem Ipsum used since the 1500s is reproduced below for those interested. Sections 1.10.32 and 1.10.33 from "de Finibus Bonorum et Malorum" by Cicero are also reproduced in their exact original form, accompanied by English versions from the 1914 translation by H. Rackham.</p>
      <p>The standard chunk of Lorem Ipsum used since the 1500s is reproduced below for those interested. Sections 1.10.32 and 1.10.33 from "de Finibus Bonorum et Malorum" by Cicero are</p>
      <div class="signature" role="img" aria-label="Handwritten signature of the sender"></div>
    </section>

    <footer class="footer-band">
      <div class="footer-company">Parcelwise HQ</div>
      <div class="footer-address">27 Alder Lane Fairview, OR 97000</div>
      <div class="footer-line">
        <span class="contact-item">
          <svg viewBox="0 0 10 10"><circle cx="5" cy="5" r="5" fill="#fff"/><path d="M3.2 2.6l1 .9-.5.8a3.5 3.5 0 0 0 1.9 1.9l.8-.5.9 1-.7.7C4.6 7.2 2.8 5.4 2.5 3.3z" fill="#355c98"/></svg>
          (555) 014-2290
        </span>
        <span class="contact-item">
          <svg viewBox="0 0 10 10"><circle cx="5" cy="5" r="5" fill="#fff"/><rect x="2.5" y="3.2" width="5" height="3.6" fill="none" stroke="#355c98" stroke-width="0.8"/><path d="M2.5 3.2L5 5.2l2.5-2" fill="none" stroke="#355c98" stroke-width="0.8"/></svg>
          mjordan@parcelwisehq.example
        </span>
        <span class="contact-item">
          <svg viewBox="0 0 10 10"><circle cx="5" cy="5" r="5" fill="#fff"/><circle cx="5" cy="5" r="2.8" fill="none" stroke="#355c98" stroke-width="0.7"/><path d="M2.2 5h5.6M5 2.2c-1.4 1.6-1.4 4 0 5.6M5 2.2c1.4 1.6 1.4 4 0 5.6" fill="none" stroke="#355c98" stroke-width="0.6"/></svg>
          www.parcelwisehq.example
        </span>
      </div>
    </footer>
  </main>
</body>
</html>
```